VocaTerrana Community/ Talent Gallery

VocaTerrana is developing a collaborative career course, with coaching and community exchange. Goal is to offer a platform where talented candidates can show their expertise and find projects, partners, and develop their online portfolios!

Here is a good example of the type of thing we hope to create with focus on sustainability focused talent to task matching
http://www.brambleforth.com/global-themes/employment-and-growth/connecting-talent-with-opportunity-in-the-digital-age

We hope to have a "grid style" gallery where it is easy to search by talent types and focus areas within the scope of "Sustainability" issues...Food/Water/Energy, Public Health, Technology, Sustainable Cities, Infrastructure, Education, Policy, Emerging Economies, Ecosystems, Social Innovation, inclusive Security, Equity Issues. For each topic/ header we hope to have candidates post their completed portfolios to exhibit resumes, biography, a case study... they may actually prepare these on other sites, but can link in OR alternately that they can easily create here, similar to "pinqo.io" ....

Hope to include a blog space titled "Rising over the Rift", where people can mix it up across these topic issues as they are interdependent and often require partners across discipline areas! If possible another area where jobs related to these issues may be posted as project or job opportunities by potential employers.

If there is a way to create a feed from various job sites that already exist...like Jobora...or http://www.greenledgerworks.com/ that would be super great. Again...sort of a portal connection to bridge the gap ....instead of candidates having to search all the time, we are hoping they can advertise their talent and employers may search here for these well presented portfolios!

Target Market(s)

Educators, Students, Career Transitioners, Employers, Professional Associations, Talent Recruiters with focus on Sustainability related Talent to Task matching!

Industry/Entity Type

Sustainability

Number of Pages Required

4 page

Font styles to use
Sans Serif

Colors
3176b5
32b8a4
add136

Requirements
Must have
• Not sure about the coded/ uncoded option here....
• Must have - grid style area where Sustainability Professionals with varied focus areas can exhibit their talent portfolios
• appear as a Talent Gallery that starts with photos & obvious organization...other tabs to be in a menu.
• ability to search both talent and task opportunity areas to help coaches or community members make matches....some topic focused category or tag words to help make them searchable...???
• consistent professional styling to existing website and new artflock postcard shared in brief/ images area
• Interactive blog space where articles, issues may be posted, discussed
• Bulletin board or feed for project opportunities to be posted where candidates may locate them and/or employers may express specific "call" for talent..These may be Short term Internships, Projects, Consulting Team Opportunity, or Jobs/ part time to full time....
Nice to have
• A calendar area where we can post networking opportunities, issues presentations where potential partners can meet the next generation leaders, attend a forum or webinar presentation.
Should not have
• Too much text on front page...Should be clean design,

```html
<!DOCTYPE html>
<html lang="en">
<head>
<meta charset="utf-8">
<title>VocaTerrana</title>
<link rel="stylesheet" href="https://fonts.googleapis.com/css2?family=Raleway:ital,wght@0,400;0,500;0,600;0,700;1,400;1,500&display=swap">
<style>
:root{
  --teal:#2aa991;
  --teal-dark:#23917c;
  --lime:#a5c92d;
  --blue:#2f6db3;
  --ink:#3d3d3d;
  --text:#5b5b5b;
  --muted:#8a8a8a;
  --band:#efefef;
  --footer:#333333;
  --line:#d9d9d9;
  --white:#ffffff;
}
*{box-sizing:border-box;margin:0;padding:0}
html,body{width:1200px;height:2456px;overflow:hidden;background:var(--white)}
body{font-family:"Raleway",Arial,sans-serif;color:var(--text);position:relative}
.abs{position:absolute}

/* header */
.site-header{position:absolute;left:0;top:0;width:1200px;height:98px;background:var(--white)}
.brand{position:absolute;left:75px;top:26px;display:flex;align-items:center;gap:14px}
.brand-dot{width:46px;height:46px;border-radius:50%;background:var(--teal)}
.brand-name{font-size:38px;font-weight:600;color:#555;letter-spacing:.2px}
.main-nav{position:absolute;top:43px;left:586px;display:flex;align-items:center;font-size:13px;font-weight:600;color:#333;letter-spacing:.3px}
.main-nav a{position:absolute;white-space:nowrap;text-decoration:none;color:inherit;top:8px}
.login-btn{position:absolute;left:1036px;top:42px;width:90px;height:36px;border-radius:18px;background:var(--teal);color:var(--white);font-size:13px;font-weight:600;display:flex;align-items:center;justify-content:center}

/* hero */
.hero{position:absolute;left:0;top:98px;width:1200px;height:540px}
.hero-photo{position:absolute;inset:0;background:linear-gradient(180deg,#4f5a3a 0%,#6d6a55 35%,#7a6c60 60%,#3c3a33 100%)}
.hero-title{position:absolute;left:0;top:252px;width:1200px;text-align:center;font-size:34px;font-weight:700;color:var(--white);letter-spacing:.3px;text-shadow:0 1px 3px rgba(0,0,0,.4)}
.search-input{position:absolute;left:254px;top:318px;width:568px;height:47px;background:var(--white);border-radius:2px;font-size:13px;font-style:italic;color:#777;padding:15px 14px}
.search-btn{position:absolute;left:835px;top:318px;width:111px;height:47px;background:var(--lime);color:var(--white);font-weight:700;font-size:16px;display:flex;align-items:center;justify-content:center}
.hero-dots{position:absolute;top:502px;left:558px;display:flex;gap:11px}
.hero-dots span{width:12px;height:12px;border-radius:50%;background:var(--white)}
.hero-dots span.active{background:var(--teal)}

/* welcome */
.welcome-title{position:absolute;left:0;top:692px;width:1200px;text-align:center;font-size:24px;font-weight:700;color:#444;letter-spacing:.3px}
.welcome-text{position:absolute;left:75px;top:742px;width:1050px;text-align:center;font-size:14.5px;line-height:24.5px;color:#5e5e5e}
.topic-tile{position:absolute;width:243px;height:155px;background:var(--teal);color:var(--white);display:flex;flex-direction:column;align-items:center;justify-content:flex-start;padding-top:30px;gap:16px;font-size:16px;font-weight:700}
.topic-tile svg{width:52px;height:52px}
.slide-arrow{position:absolute;width:22px;height:36px}

/* blog */
.blog-band{position:absolute;left:0;top:1265px;width:1200px;height:411px;background:var(--band)}
.section-title{position:absolute;font-size:23px;font-weight:700;color:#444;letter-spacing:.3px}
.blog-photo{position:absolute;left:75px;top:1368px;width:421px;height:253px;background:linear-gradient(135deg,#3a4a63 0%,#6a7c96 50%,#c9c4bc 100%)}
.post-title{position:absolute;left:524px;top:1360px;font-size:22px;font-weight:600;color:var(--blue)}
.post-text{position:absolute;left:524px;top:1398px;width:600px;font-size:14.5px;line-height:24.5px;color:#5e5e5e}
.lime-btn{position:absolute;height:46px;background:var(--lime);color:var(--white);font-size:16px;font-style:italic;display:flex;align-items:center;justify-content:center}

/* calendar */
.calendar{position:absolute;left:75px;top:1789px;width:447px;border:1px solid var(--line)}
.cal-head{height:48px;background:var(--teal);color:var(--white);display:flex;align-items:center;justify-content:space-between;padding:0 14px;font-size:18px;font-weight:700}
.cal-grid{width:100%;border-collapse:collapse;table-layout:fixed}
.cal-grid th{background:#5b5b5b;color:var(--white);font-size:13px;font-weight:700;height:27px}
.cal-grid td{height:57px;border:1px solid var(--line);text-align:center;font-size:13px;font-weight:600;color:#444}
.cal-grid td.has-event{color:var(--blue);font-weight:700}
.event{position:absolute;left:586px;width:540px}
.event-date{font-size:13px;font-weight:700;color:var(--blue);letter-spacing:.3px}
.event-text{margin-top:6px;font-size:14px;line-height:25px;color:#5e5e5e}

/* footer */
.site-footer{position:absolute;left:0;top:2225px;width:1200px;height:231px;background:var(--footer)}
.footer-brand{position:absolute;left:75px;top:54px;display:flex;align-items:center;gap:10px}
.footer-brand .brand-dot{width:38px;height:38px}
.footer-brand .brand-name{font-size:27px;color:#e8e8e8}
.copyright{position:absolute;left:75px;top:105px;font-size:12px;line-height:21px;color:#8c8c8c}
.footer-head{position:absolute;top:36px;font-size:13px;font-weight:700;color:var(--teal);letter-spacing:.5px}
.recent-list{position:absolute;left:406px;top:60px;list-style:none;font-size:13px;line-height:26px;color:#bdbdbd}
.social{position:absolute;left:704px;top:70px;display:flex;gap:6px}
.social span{width:30px;height:30px;border-radius:50%;background:#5e5e5e}
</style>
</head>
<body>

<header class="site-header">
  <div class="brand"><span class="brand-dot"></span><span class="brand-name">VocaTerrana</span></div>
  <nav class="main-nav">
    <a style="left:0">HOME</a>
    <a style="left:79px">ABOUT US</a>
    <a style="left:188px">SERVICES</a>
    <a style="left:293px">BLOG</a>
    <a style="left:370px">CONTACT</a>
  </nav>
  <div class="login-btn">LOG IN</div>
</header>

<section class="hero">
  <div class="hero-photo" role="img" aria-label="Group photo of community members gathered outdoors in a sunny garden"></div>
  <h1 class="hero-title">SEARCH COURSE, COACHING, COMMUNITY</h1>
  <div class="search-input">Search by talent, task opportunity ...</div>
  <div class="search-btn">SEARCH</div>
  <div class="hero-dots"><span class="active"></span><span></span><span></span><span></span></div>
</section>

<h2 class="welcome-title">WELCOME TO OUR WEBSITE</h2>
<p class="welcome-text">Aliquam molestie, mi et imperdiet euismod, dui purus auctor tellus, et interdum lacus lectus et ante. Sed accumsan sollicitudin sapien, sit amet adipiscing turpis gravida ac. In congue, neque ac lobortis volutpat, libero mauris varius mi, vitae suscipit ipsum ligula vitae risus. Duis aliquam nibh a dui iaculis viverra id a velit. Vivamus egestas risus in magna varius commodo. Sed semper viverra egestas. Etiam pretium porttitor lectus, vel ornare neque porta volutpat.</p>

<svg class="slide-arrow" style="left:42px;top:1035px" viewBox="0 0 22 36"><path d="M18 2 4 18l14 16" fill="none" stroke="#555" stroke-width="2.5"/></svg>
<svg class="slide-arrow" style="left:1137px;top:1035px" viewBox="0 0 22 36"><path d="M4 2l14 16L4 34" fill="none" stroke="#555" stroke-width="2.5"/></svg>

<div class="topic-tile" style="left:75px;top:884px">
  <svg viewBox="0 0 52 52" fill="none" stroke="#fff" stroke-width="3" stroke-linecap="round"><path d="M26 6v40M14 14l24 24M38 14 14 38"/><path d="M26 22c-4 5-4 9 0 10 4-1 4-5 0-10z" fill="#fff"/><path d="M30 4l-4 8h5l-4 8" stroke-width="2"/></svg>
  Food/Water/Energy</div>
<div class="topic-tile" style="left:342px;top:884px">
  <svg viewBox="0 0 52 52"><rect x="6" y="14" width="40" height="30" rx="5" fill="#fff"/><path d="M19 14V8h14v6" fill="none" stroke="#fff" stroke-width="3"/><circle cx="26" cy="29" r="9" fill="#2aa991"/><path d="M26 24v10M21 29h10" stroke="#fff" stroke-width="3"/></svg>
  Public Health</div>
<div class="topic-tile" style="left:614px;top:884px">
  <svg viewBox="0 0 52 52" fill="none" stroke="#fff" stroke-width="3"><path d="M26 6a12 12 0 0 0-7 22v6h14v-6a12 12 0 0 0-7-22z"/><path d="M20 40h12M22 45h8" stroke-linecap="round"/></svg>
  Technology</div>
<div class="topic-tile" style="left:884px;top:884px">
  <svg viewBox="0 0 52 52"><circle cx="26" cy="26" r="20" fill="#fff"/><path d="M16 16c6 2 6 8 12 8 3 4-2 8 0 14M34 12c-2 4 4 6 8 10" fill="none" stroke="#2aa991" stroke-width="3"/></svg>
  Sustainable Cities</div>

<div class="topic-tile" style="left:75px;top:1066px">
  <svg viewBox="0 0 52 52" fill="#fff"><rect x="19" y="6" width="14" height="11"/><rect x="4" y="35" width="13" height="11"/><rect x="20" y="35" width="13" height="11"/><rect x="36" y="35" width="13" height="11"/><path d="M26 17v18M10 35v-8h32v8" fill="none" stroke="#fff" stroke-width="3"/></svg>
  Infrastructure</div>
<div class="topic-tile" style="left:342px;top:1066px">
  <svg viewBox="0 0 52 52" fill="#fff"><circle cx="26" cy="12" r="7"/><path d="M8 30l18 5 18-5v16l-18 5-18-5z"/><path d="M16 28c2-6 6-8 10-8s8 2 10 8l-10 3z"/></svg>
  Education</div>
<div class="topic-tile" style="left:614px;top:1066px">
  <svg viewBox="0 0 52 52" fill="#fff"><circle cx="13" cy="15" r="6"/><circle cx="39" cy="15" r="6"/><circle cx="26" cy="20" r="7"/><path d="M2 36c0-8 5-12 11-12s8 3 8 5v7zM50 36c0-8-5-12-11-12s-8 3-8 5v7z"/><path d="M12 46c0-10 6-16 14-16s14 6 14 16z"/></svg>
  Community</div>
<div class="topic-tile" style="left:884px;top:1066px">
  <svg viewBox="0 0 52 52" fill="#fff"><path d="M26 4 4 16h44z"/><rect x="6" y="18" width="40" height="4"/><rect x="9" y="24" width="5" height="16"/><rect x="18" y="24" width="5" height="16"/><rect x="29" y="24" width="5" height="16"/><rect x="38" y="24" width="5" height="16"/><rect x="4" y="42" width="44" height="6"/></svg>
  Governance</div>

<section class="blog-band"></section>
<h2 class="section-title" style="left:75px;top:1312px">BLOG POSTS</h2>
<svg class="abs" style="left:1090px;top:1316px" width="40" height="22" viewBox="0 0 40 22"><path d="M10 3 3 11l7 8M30 3l7 8-7 8" fill="none" stroke="#555" stroke-width="2"/></svg>
<div class="blog-photo" role="img" aria-label="Panel of speakers seated at a conference table with microphones"></div>
<h3 class="post-title">Rising over the Rift</h3>
<p class="post-text">Aliquam molestie, mi et imperdiet euismod, dui purus auctor tellus, et interdum lacus lectus et ante. Sed accumsan sollicitudin sapien, sit amet adipiscing turpis gravida ac. In congue, neque ac lobortis volutpat, libero mauris varius mi, vitae suscipit ipsum ligula vitae risus. Duis aliquam nibh a dui iaculis viverra vamus egestas risus in magna varius commodo. Sed semper viverra egestas. Etiam pretium porttitor lectus, vel ornare neque porta volutpat.</p>
<div class="lime-btn" style="left:524px;top:1573px;width:214px">Continue Reading</div>

<h2 class="section-title" style="left:75px;top:1722px">CALENDAR</h2>
<div class="calendar">
  <div class="cal-head"><span style="font-weight:400">&#8249;</span><span>JUNE 2016</span><span style="font-weight:400">&#8250;</span></div>
  <table class="cal-grid">
    <tr><th>S</th><th>M</th><th>T</th><th>W</th><th>T</th><th>F</th><th>S</th></tr>
    <tr><td></td><td></td><td></td><td>1</td><td>2</td><td>3</td><td>4</td></tr>
    <tr><td>5</td><td>6</td><td class="has-event">7</td><td>8</td><td>9</td><td>10</td><td>11</td></tr>
    <tr><td>12</td><td>13</td><td>14</td><td>15</td><td>16</td><td class="has-event">17</td><td>18</td></tr>
    <tr><td>19</td><td>20</td><td>21</td><td class="has-event">22</td><td>23</td><td>24</td><td>25</td></tr>
    <tr><td>26</td><td>27</td><td>28</td><td>29</td><td>30</td><td></td><td></td></tr>
  </table>
</div>

<div class="event" style="top:1786px"><div class="event-date">JUNE 7, 2016</div><p class="event-text">Vestibulum ante ipsum primis in faucibus orci luctus et ultrices posuere cubilia lobortis turpis in odio blandit ..</p></div>
<div class="event" style="top:1888px"><div class="event-date">JUNE 7, 2016</div><p class="event-text">Vestibulum ante ipsum primis in faucibus orci luctus et ultrices posuere cubilia lobortis turpis in odio blandit ..</p></div>
<div class="event" style="top:1989px"><div class="event-date">JUNE 7, 2016</div><p class="event-text">Vestibulum ante ipsum primis in faucibus orci luctus et ultrices posuere cubilia lobortis turpis in odio blandit ..</p></div>
<div class="lime-btn" style="left:586px;top:2105px;width:214px">View All Events</div>

<footer class="site-footer">
  <div class="footer-brand"><span class="brand-dot"></span><span class="brand-name">VocaTerrana</span></div>
  <p class="copyright">© 2016 VocaTerrana<br>All Right Reserved</p>
  <div class="footer-head" style="left:406px">RECENT POSTS</div>
  <ul class="recent-list">
    <li>Duis aliquam nibh a dui iaculis</li>
    <li>Viverra id a velit. Vivamus egestas</li>
    <li>Risus in magna</li>
    <li>Etiam pretium porttitor lectus</li>
  </ul>
  <div class="footer-head" style="left:704px">CONNECT US</div>
  <div class="social"><span></span><span></span><span></span><span></span><span></span><span></span></div>
</footer>

</body>
</html>
```